Stationary (Branding) for Plumbing & Heating Buisness
Dunmore Kettle Ltd
Use same font as used in my logo
Dunmore Kettle
Unit 8 Larchfield Ind Est.
Glanrhosydd
Brynhafod
Cwmderwen
dunmore@quietembergrid.co.uk
www.dunmorekettle.com
Looking for complete stationary with A4 letter head, business cards and so on using the logo provided. Modern, clean and eco friendly is the image we are looking for.
The font used in the logo is not final and maybe changed so please ignore that.
Would like to see the logo on the back of the card with spot UV effect.
The font in this logo is not final and may change
plumbing
renewables
heating

```html
<!DOCTYPE html>
<html lang="en">
<head>
<meta charset="utf-8">
<title>Dunmore Kettle Ltd – Stationery</title>
<link rel="stylesheet" href="https://fonts.googleapis.com/css2?family=Open+Sans:wght@400;600;700&display=swap">
<style>
:root{
  --backdrop:#6e4a2c;
  --paper:#ffffff;
  --paper-shade:#eef0f2;
  --green:#8cc63f;
  --green-dark:#5e9e2a;
  --blue:#1f6eb5;
  --blue-dark:#174f86;
  --ink:#3a3a3a;
  --ink-soft:#8a8a8a;
  --sign:#c9cdd2;
}
*{margin:0;padding:0;box-sizing:border-box}
html,body{width:1200px;height:314px;overflow:hidden}
body{background:var(--backdrop);font-family:"Open Sans",Arial,sans-serif;color:var(--ink);position:relative}
.sheet{position:absolute;background:var(--paper);box-shadow:0 2px 6px rgba(0,0,0,.35);overflow:hidden}

/* brand lockup */
.brand{display:flex;align-items:center;gap:4px}
.brand-dot{width:12px;height:12px;border-radius:50%;background:var(--green);flex:none}
.brand-name{font-weight:700;color:var(--green-dark);font-size:7px;white-space:nowrap}
.brand.large{flex-direction:column;gap:6px}
.brand.large .brand-dot{width:30px;height:30px}
.brand.large .brand-name{font-size:9px}

/* concept title */
.concept-title{position:absolute;left:150px;top:112px;color:#fff}
.concept-title .client{font-weight:700;font-size:13px;color:var(--green)}
.concept-title .label{font-size:10px;letter-spacing:.5px}

/* business cards */
.card-front{left:22px;top:112px;width:118px;height:66px;padding:10px}
.card-front .tagline{position:absolute;left:10px;bottom:14px;font-size:4.5px;color:var(--ink-soft);letter-spacing:.4px}
.card-front .band{position:absolute;left:0;right:0;bottom:0;height:6px;background:var(--green)}
.card-back{left:22px;top:196px;width:118px;height:96px;background:var(--paper-shade);display:flex;align-items:center;justify-content:center}
.card-detail{left:150px;top:202px;width:124px;height:78px;padding:10px}
.card-detail .brand{position:absolute;right:8px;top:10px}
.card-detail .person{position:absolute;left:10px;top:34px;font-size:5px;line-height:1.5}
.card-detail .person b{font-size:6px}
.card-detail .band{position:absolute;left:0;right:0;bottom:0;height:5px;background:var(--blue)}

/* letterheads */
.letter{top:42px;width:216px;height:264px;padding:14px 16px}
.letter.one{left:336px}
.letter.two{left:576px}
.letter .head{display:flex;justify-content:space-between;align-items:flex-start}
.letter .contact{font-size:3.6px;line-height:1.5;text-align:right;color:var(--ink-soft)}
.letter .recipient{margin-top:18px;font-size:3.8px;line-height:1.55}
.letter .body{margin-top:10px;font-size:3.6px;line-height:1.7;color:#555}
.letter .body p{margin-bottom:6px}
.letter .signature{width:50px;height:12px;background:var(--sign);border-radius:6px;margin:4px 0 3px}
.letter .foot{position:absolute;left:0;right:0;bottom:0;height:12px}
.letter .foot svg{display:block}

/* right cluster */
.card-small{left:816px;top:120px;width:86px;height:50px;padding:8px}
.card-small .band{position:absolute;left:0;right:0;bottom:0;height:4px;background:var(--green)}
.comp-slip{left:816px;top:190px;width:108px;height:86px;padding:10px}
.comp-slip .label{position:absolute;left:10px;top:32px;font-size:5px;color:var(--ink-soft)}
.comp-slip .foot{position:absolute;left:0;right:0;bottom:0;height:10px}
.envelope{width:262px;height:118px}
.envelope.open{left:912px;top:92px;background:var(--paper)}
.envelope.closed{left:932px;top:190px;height:112px;padding:12px}
.envelope .addr{position:absolute;right:18px;bottom:24px;font-size:5px;line-height:1.5;color:var(--ink-soft);text-align:right}
.envelope .foot{position:absolute;left:0;right:0;bottom:0;height:12px}
</style>
</head>
<body>

<div class="concept-title">
  <div class="client">Dunmore Kettle Ltd</div>
  <div class="label">Stationery Concept</div>
</div>

<section class="sheet card-front">
  <div class="brand"><span class="brand-dot"></span><span class="brand-name">Dunmore Kettle Ltd</span></div>
  <div class="tagline">plumbing · renewables · heating</div>
  <div class="band"></div>
</section>

<section class="sheet card-back">
  <div class="brand large"><span class="brand-dot"></span><span class="brand-name">Dunmore Kettle Ltd</span></div>
</section>

<section class="sheet card-detail">
  <div class="brand"><span class="brand-dot"></span><span class="brand-name">Dunmore Kettle Ltd</span></div>
  <div class="person"><b>Dunmore Kettle</b><br>Director<br>T: 01495 700 318<br>dunmore@quietembergrid.co.uk<br>www.dunmorekettle.com</div>
  <div class="band"></div>
</section>

<article class="sheet letter one">
  <div class="head">
    <div class="brand"><span class="brand-dot"></span><span class="brand-name">Dunmore Kettle Ltd</span></div>
    <div class="contact">Unit 8 Larchfield Ind Est.<br>Glanrhosydd<br>Brynhafod<br>Cwmderwen<br>T: 01495 700 318<br>dunmore@quietembergrid.co.uk<br>www.dunmorekettle.com</div>
  </div>
  <div class="recipient"><b>Recipient Name</b><br>Street Address<br>Town, Postcode</div>
  <div class="body">
    <p>Dear Customer,</p>
    <p>Thank you for choosing us for your plumbing and heating work. We are pleased to confirm the details of your upcoming installation below.</p>
    <p>Our engineers will arrive on the agreed date and complete all work to current standards, leaving your home clean and safe.</p>
    <p>Please contact our office if you have any questions before the visit.</p>
    <p>Yours sincerely,</p>
    <div class="signature" role="img" aria-label="handwritten signature"></div>
    <p>Dunmore Kettle<br>Director</p>
  </div>
  <div class="foot"><svg width="216" height="12" viewBox="0 0 216 12" preserveAspectRatio="none"><path d="M0 12 L0 5 Q108 -2 216 5 L216 12Z" fill="var(--green)"/><rect y="9" width="216" height="3" fill="var(--blue)"/></svg></div>
</article>

<article class="sheet letter two">
  <div class="head">
    <div class="brand"><span class="brand-dot"></span><span class="brand-name">Dunmore Kettle Ltd</span></div>
    <div class="contact">Unit 8 Larchfield Ind Est.<br>Glanrhosydd<br>Brynhafod<br>Cwmderwen<br>T: 01495 700 318<br>dunmore@quietembergrid.co.uk<br>www.dunmorekettle.com</div>
  </div>
  <div class="recipient"><b>Recipient Name</b><br>Street Address<br>Town, Postcode</div>
  <div class="body">
    <p>Dear Customer,</p>
    <p>Thank you for choosing us for your plumbing and heating work. We are pleased to confirm the details of your upcoming installation below.</p>
    <p>Our engineers will arrive on the agreed date and complete all work to current standards, leaving your home clean and safe.</p>
    <p>Please contact our office if you have any questions before the visit.</p>
    <p>Yours sincerely,</p>
    <div class="signature" role="img" aria-label="handwritten signature"></div>
    <p>Dunmore Kettle<br>Director</p>
  </div>
  <div class="foot"><svg width="216" height="12" viewBox="0 0 216 12" preserveAspectRatio="none"><path d="M0 12 L0 5 Q108 -2 216 5 L216 12Z" fill="var(--green)"/><rect y="9" width="216" height="3" fill="var(--blue)"/></svg></div>
</article>

<section class="sheet card-small">
  <div class="brand"><span class="brand-dot"></span><span class="brand-name">Dunmore Kettle Ltd</span></div>
  <div class="band"></div>
</section>

<section class="sheet envelope open">
  <svg width="262" height="118" viewBox="0 0 262 118" preserveAspectRatio="none">
    <rect width="262" height="118" fill="var(--paper)"/>
    <path d="M0 0 L262 0 L131 58Z" fill="var(--blue)"/>
    <path d="M0 0 L131 58 L262 0 L262 8 L131 64 L0 8Z" fill="var(--blue-dark)"/>
    <path d="M0 118 L0 104 Q131 88 262 104 L262 118Z" fill="var(--green)"/>
  </svg>
</section>

<section class="sheet comp-slip">
  <div class="brand"><span class="brand-dot"></span><span class="brand-name">Dunmore Kettle Ltd</span></div>
  <div class="label">With Compliments</div>
  <div class="foot"><svg width="108" height="10" viewBox="0 0 108 10" preserveAspectRatio="none"><path d="M0 10 L0 4 Q54 -2 108 4 L108 10Z" fill="var(--green)"/><rect y="8" width="108" height="2" fill="var(--blue)"/></svg></div>
</section>

<section class="sheet envelope closed">
  <div class="brand"><span class="brand-dot"></span><span class="brand-name">Dunmore Kettle Ltd</span></div>
  <div class="addr">Unit 8 Larchfield Ind Est.<br>Glanrhosydd</div>
  <div class="foot"><svg width="262" height="12" viewBox="0 0 262 12" preserveAspectRatio="none"><path d="M0 12 L0 5 Q131 -2 262 5 L262 12Z" fill="var(--green)"/><rect y="9" width="262" height="3" fill="var(--blue)"/></svg></div>
</section>

</body>
</html>
```